Flyer, poster, banner and social media titles designs for Community Mending Chartre

The Harbourline Charter for Community Mending provide a nationally agreed framework to guide recovery policy and practice across Australia. The Principles support recovery practitioners, governments, non-government organisations and communities to deliver effective, community-centred recovery outcomes.
The Principles have recently been refreshed through extensive consultation and we require a contemporary visual identity and design suite that will increase awareness, engagement and practical application of the Principles.
The redesign will cover:
• A4 Brochure (primary publication)
• A3 Poster
• Pull up banner
• Social Media Tiles
The new design should:
• Create a recognisable brand for the Harbourline Charter.
• Appeal to both experienced and emerging recovery practitioners.
• Reflect contemporary disaster recovery practice.
• Feel people-focused rather than government-focused.
• Support future resources such as videos, implementation guides, presentations and workshop materials.
• Remain relevant for several years without requiring a major redesign.
Target Audience
• Disaster recovery practitioners
• Government agencies
• Non-government organisations
• Community recovery workers
• Recovery managers and leaders
• Community stakeholders and volunteers
The visual identity should reflect the six Principles:
• Understanding Context
• Recognising Complexity
• Community-Centred Approaches
• Coordination
• Communication
• Capacity Building
The design should communicate:
• Recovery is centred on people and communities.
• Recovery is collaborative and involves many sectors.
• Recovery is adaptive, inclusive and evidence-informed.
• Recovery supports resilience and long-term wellbeing.
• The Principles provide practical guidance for recovery practice.
We are looking for:
• Modern and professional
• Warm and approachable
• Human-centred
• Inclusive and accessible
• Australian in context
• Visually engaging
• Suitable for print and digital use
We would like to avoid:
• Images of disaster destruction
• Emergency response imagery (fire trucks, flashing lights, etc.)
• Overly corporate or bureaucratic designs
• Designs that focus on deficits rather than recovery and growth
Consider themes such as:
• Connection and collaboration
• Communities and people
• Growth, recovery and renewal
Accessibility
Designs should:
• Meet accessibility best practice
• Use clear typography
• Achieve strong colour contrast
• Be suitable for both digital and print formats

Deliverables
1. Principles Brochure
• A4 trifold size x 2 (online and print friendly version)
• A side to include cover side, logos side and overview of principles.
• B side full details of the principles
• Graphic to highlight the 3 c’s concept (RECOVERY Context, complexity, community centred, coordinate, communicate and capacity). Currently 3 circles.
• Can be printed and distributed electronically
2. Poster
• A1 and A3 versions
• Suitable for office and workshop display
3. Pull-Up Banner - 850 mm (W) × 2000 mm (H)
• Conference and event use
• High visual impact
• Strong branding and concise messaging
4. Social Media Tiles x 3

We are providing an extension and increasing the budget following feedback from designers. We are wanting the resources to look and feel different from the existing designs, considering either a different colour palette in the designs or different motif with the leave design. Any nature based designs should consider the Australian fauna or flora. Also suggest avoiding images in the designs. The principles are not numbered or liner in the concept of how they function. Happy to answer any further questions and thank you for your suggested concepts.

Disaster recovery practitioners, Government agencies , Non-government organisations, Community recovery workers and Community stakeholders and volunteers

Disaster recovery

• Modern, warm, visually engaging, human-centred, Australian in context and different to the current design.
• Symbols for each principles
• Images of disaster destruction, Emergency response imagery, Overly corporate or bureaucratic designs, Designs that focus on deficits rather than recovery and growth, avoid too much black

```html
<!DOCTYPE html>
<html lang="en">
<head>
<meta charset="utf-8">
<title>Harbourline Charter for Community Mending – Design Suite</title>
<link href="https://fonts.googleapis.com/css2?family=Source+Sans+3:wght@400;600;700&display=swap" rel="stylesheet">
<style>
:root{
  --bg:#f2eee5;
  --forest:#0f3d33;
  --forest-2:#17503f;
  --leaf:#7d9b2e;
  --cream:#f7f2e6;
  --paper:#fbf8f1;
  --ink:#24302c;
  --olive:#5c7a28;
  --teal:#1f5c58;
  --ember:#d4502a;
  --amber:#e68f26;
  --ocean:#1e5f7c;
  --plum:#6a4a88;
  --clay:#d0651f;
  --moss:#3f7a45;
}
*{box-sizing:border-box;margin:0;padding:0}
html,body{width:1200px;height:800px;overflow:hidden;background:var(--bg)}
body{font-family:"Source Sans 3",Arial,sans-serif;color:var(--ink)}
.canvas{position:relative;width:1200px;height:800px;overflow:hidden;background:var(--bg)}
.abs{position:absolute}
.piece{position:absolute;overflow:hidden;box-shadow:0 2px 6px rgba(0,0,0,.12)}
.caption{position:absolute;font-size:10px;letter-spacing:.12em;text-transform:uppercase;color:#333;transform:translateX(-50%);white-space:nowrap}
.kicker{font-size:10px;letter-spacing:.05em;text-transform:uppercase;color:#fff}
.title{font-weight:600;line-height:.98;color:#fff;letter-spacing:-.01em}
.title .accent{color:var(--leaf);display:block}
.tagline{color:#fff;line-height:1.35}
.art{position:absolute}
.icon{width:100%;height:100%;display:block}
.badge{border-radius:50%;display:flex;align-items:center;justify-content:center}
.badge svg{width:56%;height:56%}
.c-context{background:var(--olive)} .t-context{color:var(--olive)}
.c-complex{background:var(--teal)} .t-complex{color:var(--teal)}
.c-community{background:var(--ember)} .t-community{color:var(--ember)}
.c-coord{background:var(--amber)} .t-coord{color:var(--amber)}
.c-comm{background:var(--ocean)} .t-comm{color:var(--ocean)}
.c-capacity{background:var(--plum)} .t-capacity{color:var(--plum)}

/* Brochure */
.brochure{left:12px;top:14px;width:521px;height:423px}
.panel{position:absolute;top:0;height:100%}
.panel-cover{left:0;width:178px;background:var(--forest)}
.panel-partners{left:178px;width:172px;background:var(--paper)}
.panel-overview{left:350px;width:171px;background:var(--cream)}
.partners-head{font-size:9px;font-weight:700;letter-spacing:.06em;text-align:center;margin-top:28px;line-height:1.2;text-transform:uppercase}
.partner-list{list-style:none;margin:16px 0 0 34px}
.partner{display:flex;align-items:center;gap:7px;height:37px;font-size:8px;line-height:1.15;color:var(--ink)}
.partner .mark{width:16px;height:16px;flex:none;background:var(--teal);border-radius:50%}
.partner .mark.sq{border-radius:2px;background:var(--olive)}
.overview-head{font-size:11px;font-weight:700;letter-spacing:.03em;color:var(--ink);line-height:1.2;margin:32px 14px 0 18px;text-transform:uppercase}
.overview-head span{color:var(--olive);display:block;font-size:13px}
.overview-copy{margin:12px 14px 0 18px;font-size:7.3px;line-height:1.6;color:#33413c}
.overview-copy p{margin-bottom:9px}

/* 3C */
.concept{left:12px;top:472px;width:486px;height:278px;background:var(--paper)}
.concept-title{position:absolute;left:0;width:252px;top:13px;text-align:center;font-size:11px;font-weight:600;letter-spacing:.06em}
.concept-divider{position:absolute;left:252px;top:18px;width:1px;height:228px;background:#cfc8b8}
.concept-list{position:absolute;left:286px;top:16px;list-style:none}
.concept-list li{display:flex;align-items:center;gap:10px;height:37px;font-size:9.5px;font-weight:600;letter-spacing:.04em;line-height:1.25;text-transform:uppercase}
.concept-list .badge{width:30px;height:30px;flex:none}

/* Poster */
.poster{left:559px;top:14px;width:386px;height:558px;background:var(--cream)}
.poster-head{position:absolute;left:0;top:0;width:100%;height:190px}
.poster-text{position:absolute;left:29px;top:30px}
.principles{position:absolute;left:29px;top:175px;list-style:none;width:340px}
.principles li{display:flex;gap:12px;height:52px;align-items:flex-start}
.principles .badge{width:44px;height:44px;flex:none}
.principles h3{font-size:11px;font-weight:600;letter-spacing:.03em;text-transform:uppercase;margin-top:3px}
.principles p{font-size:7.6px;line-height:1.35;color:#33413c;margin-top:2px;max-width:220px}
.poster-foot{position:absolute;left:0;bottom:0;width:100%;height:62px}
.foot-text{position:absolute;left:74px;top:22px;font-size:8.6px;line-height:1.6;color:#fff}
.foot-text span{color:#a7c15a}

/* Tiles */
.tile{top:602px;height:148px}
.tile-text{position:absolute;left:31px;top:22px;font-size:16.5px;line-height:1.2;font-weight:500}

/* Banner */
.banner{left:973px;top:31px;width:209px;height:704px;background:var(--cream)}
.banner-list{position:absolute;left:18px;top:214px;list-style:none}
.banner-list li{display:flex;align-items:center;gap:14px;height:50px;font-size:12.2px;font-weight:600;letter-spacing:.02em;line-height:1.15;text-transform:uppercase}
.banner-list .badge{width:40px;height:40px;flex:none}
.banner-foot-text{position:absolute;left:0;width:100%;top:592px;text-align:center;font-size:10px;line-height:1.45;color:#fff}
</style>
</head>
<body>
<svg width="0" height="0" style="position:absolute" aria-hidden="true">
  <defs>
    <symbol id="i-context" viewBox="0 0 24 24"><g fill="none" stroke="#fff" stroke-width="1.6" stroke-linecap="round"><circle cx="6" cy="8" r="2.5"/><circle cx="12" cy="6" r="2.5"/><circle cx="18" cy="8" r="2.5"/><path d="M2 19c0-3.5 2-5.5 4-5.5M22 19c0-3.5-2-5.5-4-5.5M7 20c0-4 2.2-7 5-7s5 3 5 7z"/></g></symbol>
    <symbol id="i-complex" viewBox="0 0 24 24"><g fill="none" stroke="#fff" stroke-width="1.6"><circle cx="12" cy="12" r="2.6"/><circle cx="5" cy="5" r="2.4"/><circle cx="19" cy="5" r="2.4"/><circle cx="5" cy="19" r="2.4"/><circle cx="19" cy="19" r="2.4"/><path d="M7 7l3 3M17 7l-3 3M7 17l3-3M17 17l-3-3"/></g></symbol>
    <symbol id="i-community" viewBox="0 0 24 24"><g fill="none" stroke="#fff" stroke-width="1.6" stroke-linecap="round"><circle cx="12" cy="12" r="9"/><circle cx="12" cy="12" r="3"/><path d="M12 3v4M12 17v4M3 12h4M17 12h4"/></g></symbol>
    <symbol id="i-coord" viewBox="0 0 24 24"><g fill="none" stroke="#fff" stroke-width="1.6"><rect x="3" y="3" width="8" height="8" rx="1"/><rect x="13" y="3" width="8" height="8" rx="1"/><rect x="3" y="13" width="8" height="8" rx="1"/><rect x="13" y="13" width="8" height="8" rx="1"/></g></symbol>
    <symbol id="i-comm" viewBox="0 0 24 24"><path d="M4 5h16v10H10l-5 4v-4H4z" fill="none" stroke="#fff" stroke-width="1.6" stroke-linejoin="round"/></symbol>
    <symbol id="i-capacity" viewBox="0 0 24 24"><g fill="none" stroke="#fff" stroke-width="1.6" stroke-linecap="round"><path d="M12 21V11"/><path d="M12 13C12 7 8 4 4 4c0 5 3 9 8 9z"/><path d="M12 13c0-6 4-9 8-9 0 5-3 9-8 9z"/></g></symbol>
    <symbol id="i-circle" viewBox="0 0 24 24"><g fill="none" stroke="#fff" stroke-width="1.3" stroke-linecap="round"><circle cx="12" cy="6" r="2.5"/><circle cx="5" cy="10" r="2"/><circle cx="19" cy="10" r="2"/><path d="M7 21c0-5 2-8 5-8s5 3 5 8M1.5 20c0-4 1.5-6 3.5-6M22.5 20c0-4-1.5-6-3.5-6"/></g></symbol>
  </defs>
</svg>

<main class="canvas">

  <!-- A4 brochure, side A -->
  <section class="piece brochure" aria-label="A4 brochure side A">
    <div class="panel panel-cover">
      <div class="abs" style="left:21px;top:52px">
        <p class="kicker" style="font-size:9.5px">Harbourline Charter for</p>
        <h1 class="title" style="font-size:33px;margin-top:6px">Community<span class="accent">Mending</span></h1>
        <p class="tagline" style="font-size:11px;margin-top:14px;width:130px">Guiding effective, community-centred recovery across Australia</p>
      </div>
      <svg class="abs" style="left:0;bottom:0" width="178" height="220" viewBox="0 0 178 220" aria-hidden="true">
        <path d="M178 20C120 60 150 140 60 170 30 180 10 200 0 220h178z" fill="#2c6a4c"/>
        <path d="M178 80C140 110 160 170 90 200 70 208 60 215 55 220h123z" fill="#e9e2c8"/>
      </svg>
      <div class="art" role="img" aria-label="Illustration of native gum leaves and gum nuts on a branch" style="left:12px;top:300px;width:120px;height:120px;border-radius:50% 50% 10% 50%;background:radial-gradient(circle at 55% 45%,#7fa860 0%,#4f7f48 45%,rgba(15,61,51,0) 75%)"></div>
    </div>
    <div class="panel panel-partners">
      <p class="partners-head">Partners in<br>development</p>
      <ul class="partner-list">
        <li class="partner"><span class="mark sq"></span>Commonwealth Office<br>of Civic Affairs</li>
        <li class="partner"><span class="mark sq"></span>Office of the Chief<br>Legal Counsel</li>
        <li class="partner"><span class="mark"></span>Helping Hands<br>Relief</li>
        <li class="partner"><span class="mark"></span>Resilience Services<br>Network</li>
        <li class="partner"><span class="mark sq"></span>Southern Isle<br>Council</li>
        <li class="partner"><span class="mark"></span>Top End<br>Council</li>
        <li class="partner"><span class="mark sq"></span>Sunshine State<br>Council</li>
        <li class="partner"><span class="mark"></span>Southern Coast<br>Council</li>
        <li class="partner"><span class="mark"></span>Community Care<br>Reference Circle</li>
      </ul>
    </div>
    <div class="panel panel-overview">
      <h2 class="overview-head">Harbourline Charter for<span>Community Mending</span></h2>
      <div class="overview-copy">
        <p>The Harbourline Charter for Community Mending provides a nationally agreed framework to guide recovery policy and practice across Australia.</p>
        <p>The Principles support recovery practitioners, governments, non-government organisations and communities to deliver effective, community-centred recovery outcomes.</p>
        <p>The Principles reflect contemporary practice and are underpinned by collaboration, adaptability, inclusion and evidence-informed approaches.</p>
        <p>They provide practical guidance for building resilient communities and supporting long-term recovery and wellbeing.</p>
      </div>
      <svg class="abs" style="left:0;bottom:0" width="171" height="90" viewBox="0 0 171 90" aria-hidden="true">
        <path d="M0 60C50 40 90 80 171 30v60H0z" fill="#9bbf5a"/>
        <path d="M0 75C60 60 110 90 171 60v30H0z" fill="#3f7a45"/>
      </svg>
      <div class="art" role="img" aria-label="Illustration of a eucalyptus sprig with buds" style="left:100px;top:330px;width:60px;height:55px;border-radius:50%;background:radial-gradient(circle,#6f9a4d 0%,rgba(111,154,77,0) 70%)"></div>
    </div>
  </section>
  <p class="caption" style="left:272px;top:447px">A4 Brochure – Side A</p>

  <!-- 3C concept -->
  <section class="piece concept" aria-label="The 3C concept graphic">
    <h2 class="concept-title">THE 3C CONCEPT</h2>
    <svg class="abs" style="left:0;top:0" width="252" height="278" viewBox="0 0 252 278">
      <circle cx="105" cy="132" r="78" fill="var(--moss)" opacity=".92"/>
      <circle cx="168" cy="132" r="78" fill="var(--leaf)" opacity=".85"/>
      <circle cx="136" cy="200" r="78" fill="var(--clay)" opacity=".9"/>
      <circle cx="136" cy="152" r="32" fill="#fff"/>
      <g font-family="Source Sans 3, Arial, sans-serif" fill="#fff" text-anchor="middle">
        <text x="80" y="103" font-size="10" font-weight="600">CONTEXT</text>
        <text x="80" y="116" font-size="8">Understand the</text>
        <text x="80" y="127" font-size="8">community</text>
        <text x="192" y="103" font-size="10" font-weight="600">COMPLEXITY</text>
        <text x="192" y="116" font-size="8">Recognise the</text>
        <text x="192" y="127" font-size="8">nature of</text>
        <text x="192" y="138" font-size="8">disasters</text>
        <text x="136" y="223" font-size="10" font-weight="600">COMMUNITY-CENTRED</text>
        <text x="136" y="236" font-size="8">Place community at</text>
        <text x="136" y="247" font-size="8">the heart</text>
        <text x="136" y="156" font-size="10" font-weight="600" fill="#1b2a25">RECOVERY</text>
      </g>
    </svg>
    <div class="concept-divider"></div>
    <ul class="concept-list">
      <li class="t-context"><span class="badge c-context"><svg><use href="#i-context"/></svg></span>Understand context</li>
      <li class="t-complex"><span class="badge c-complex"><svg><use href="#i-complex"/></svg></span>Recognise complexity</li>
      <li class="t-community"><span class="badge c-community"><svg><use href="#i-community"/></svg></span>Use community-<br>centred approaches</li>
      <li class="t-coord"><span class="badge c-coord"><svg><use href="#i-coord"/></svg></span>Coordinate all<br>activities</li>
      <li class="t-comm"><span class="badge c-comm"><svg><use href="#i-comm"/></svg></span>Communicate<br>effectively</li>
      <li class="t-capacity"><span class="badge c-capacity"><svg><use href="#i-capacity"/></svg></span>Recognise and<br>build capacity</li>
    </ul>
  </section>

  <!-- A3 poster -->
  <section class="piece poster" aria-label="A3 poster">
    <svg class="poster-head" viewBox="0 0 386 190" preserveAspectRatio="none" aria-hidden="true">
      <path d="M0 0h386v120C300 135 240 200 150 170 90 152 40 160 0 172z" fill="#7d9b2e"/>
      <path d="M0 0h386v105C300 120 240 180 150 158 90 144 40 150 0 160z" fill="var(--forest)"/>
    </svg>
    <div class="art" role="img" aria-label="Illustration of a red grevillea flower with gum leaves" style="left:230px;top:10px;width:150px;height:120px;border-radius:50%;background:radial-gradient(circle at 45% 50%,#d9472b 0%,#b8452a 22%,#6f9a4d 45%,rgba(15,61,51,0) 72%)"></div>
    <div class="poster-text">
      <p class="kicker" style="font-size:10px">Harbourline Charter for</p>
      <h1 class="title" style="font-size:37px;margin-top:5px">Community<span class="accent">Mending</span></h1>
      <p class="tagline" style="font-size:10.5px;margin-top:10px">Guiding effective, community-centred<br>recovery across Australia.</p>
    </div>
    <ul class="principles">
      <li><span class="badge c-context"><svg><use href="#i-context"/></svg></span><div><h3 class="t-context">Understand context</h3><p>Successful recovery is based on an understanding of community context, history, values and strengths.</p></div></li>
      <li><span class="badge c-complex"><svg><use href="#i-complex"/></svg></span><div><h3 class="t-complex">Recognise complexity</h3><p>Successful recovery is responsive to the complex and evolving nature of disasters and their impacts.</p></div></li>
      <li><span class="badge c-community"><svg><use href="#i-community"/></svg></span><div><h3 class="t-community">Use community-centred approaches</h3><p>Successful recovery is community-centred, responsive and flexible, engaging with community and supporting them to move forward.</p></div></li>
      <li><span class="badge c-coord"><svg><use href="#i-coord"/></svg></span><div><h3 class="t-coord">Coordinate all activities</h3><p>Successful recovery requires a planned, coordinated and adaptive approach between community and partner agencies, based on continuing assessment of needs.</p></div></li>
      <li><span class="badge c-comm"><svg><use href="#i-comm"/></svg></span><div><h3 class="t-comm">Communicate effectively</h3><p>Successful recovery is built on effective communication between the affected community and other partners.</p></div></li>
      <li><span class="badge c-capacity"><svg><use href="#i-capacity"/></svg></span><div><h3 class="t-capacity">Recognise and build capacity</h3><p>Successful recovery recognises, supports and builds on individual, community and organisational capacity and resilience.</p></div></li>
    </ul>
    <div class="art" role="img" aria-label="Illustration of native leaves and flower buds" style="left:310px;top:430px;width:76px;height:80px;border-radius:50% 0 0 50%;background:radial-gradient(circle at 70% 50%,#4f7f48 0%,rgba(79,127,72,0) 70%)"></div>
    <svg class="poster-foot" viewBox="0 0 386 62" preserveAspectRatio="none" aria-hidden="true">
      <path d="M0 8C120 0 260 14 386 4v58H0z" fill="var(--forest)"/>
    </svg>
    <svg class="abs" style="left:26px;top:512px" width="38" height="34" aria-hidden="true"><use href="#i-circle"/></svg>
    <p class="foot-text" style="top:518px">Stronger together. <span>Building resilient communities.</span><br>Supporting long-term recovery and wellbeing.</p>
  </section>
  <p class="caption" style="left:717px;top:580px">A3 Poster</p>

  <!-- Social media tiles -->
  <section class="piece tile" style="left:512px;width:130px;background:var(--forest)" aria-label="Social media tile one">
    <div class="art" role="img" aria-label="Illustration of gum leaves and buds along the edge" style="left:-10px;top:0;width:30px;height:148px;background:linear-gradient(#3f7a45,#6f9a4d)"></div>
    <svg class="abs" style="left:0;bottom:0" width="130" height="40" aria-hidden="true"><path d="M40 40C70 20 100 30 130 0v40z" fill="#e9e2c8"/></svg>
    <p class="tile-text" style="left:30px;top:20px;font-size:15px;color:#fff">Recovery<br>is about<br><span style="color:#a7c15a">people</span> and<br><span style="color:#a7c15a">communities.</span></p>
    <svg class="abs" style="left:52px;top:114px" width="26" height="24" aria-hidden="true"><use href="#i-circle"/></svg>
  </section>
  <section class="piece tile" style="left:652px;width:134px;background:var(--cream)" aria-label="Social media tile two">
    <div class="art" role="img" aria-label="Illustration of eucalyptus leaves and a red bloom" style="left:90px;top:0;width:44px;height:70px;border-radius:0 0 0 60%;background:radial-gradient(circle at 70% 30%,#c9542d 0%,#6f9a4d 45%,rgba(111,154,77,0) 75%)"></div>
    <svg class="abs" style="left:0;bottom:0" width="134" height="50" aria-hidden="true"><path d="M60 50C90 30 110 40 134 10v40z" fill="var(--teal)"/></svg>
    <p class="tile-text" style="left:24px;top:28px;font-size:15px;color:var(--forest)">Working<br>together for<br><span style="color:var(--olive)">resilient<br>communities.</span></p>
    <svg class="abs" style="left:46px;top:116px" width="26" height="24" aria-hidden="true"><g style="filter:invert(1)"><use href="#i-circle"/></g></svg>
  </section>
  <section class="piece tile" style="left:800px;width:141px;background:var(--forest)" aria-label="Social media tile three">
    <div class="art" role="img" aria-label="Illustration of a red grevillea flower with leaves" style="left:70px;top:70px;width:75px;height:80px;border-radius:50%;background:radial-gradient(circle,#d9472b 0%,#8e5a2c 30%,#4f7f48 50%,rgba(15,61,51,0) 75%)"></div>
    <p class="tile-text" style="left:14px;top:18px;font-size:15px;color:#fff">Guiding<br>recovery<br>for a <span style="color:#a7c15a">stronger</span><br><span style="color:#a7c15a">tomorrow.</span></p>
    <svg class="abs" style="left:16px;top:104px" width="30" height="30" aria-hidden="true"><use href="#i-capacity"/></svg>
  </section>
  <p class="caption" style="left:715px;top:764px">Social Media Tiles</p>

  <!-- Pull up banner -->
  <section class="piece banner" aria-label="Pull up banner">
    <svg class="abs" style="left:0;top:0" width="209" height="215" aria-hidden="true">
      <path d="M0 0h209v160C150 170 110 210 60 196 30 188 12 192 0 198z" fill="#7d9b2e"/>
      <path d="M0 0h209v148C150 160 110 196 60 184 30 178 12 180 0 186z" fill="var(--forest)"/>
    </svg>
    <div class="art" role="img" aria-label="Illustration of gum leaves" style="left:150px;top:0;width:59px;height:90px;border-radius:0 0 0 60%;background:radial-gradient(circle at 70% 40%,#6f9a4d 0%,rgba(111,154,77,0) 70%)"></div>
    <div class="abs" style="left:23px;top:52px">
      <p class="kicker" style="font-size:9.5px">Harbourline Charter for</p>
      <h1 class="title" style="font-size:33px;margin-top:5px">Community<span class="accent">Mending</span></h1>
      <p class="tagline" style="font-size:10.5px;margin-top:10px">Guiding effective,<br>community-centred<br>recovery across Australia.</p>
    </div>
    <ul class="banner-list">
      <li class="t-context"><span class="badge c-context"><svg><use href="#i-context"/></svg></span>Understand<br>context</li>
      <li class="t-complex"><span class="badge c-complex"><svg><use href="#i-complex"/></svg></span>Recognise<br>complexity</li>
      <li class="t-community"><span class="badge c-community"><svg><use href="#i-community"/></svg></span>Use<br>community-centred<br>approaches</li>
      <li class="t-coord"><span class="badge c-coord"><svg><use href="#i-coord"/></svg></span>Coordinate<br>all activities</li>
      <li class="t-comm"><span class="badge c-comm"><svg><use href="#i-comm"/></svg></span>Communicate<br>effectively</li>
      <li class="t-capacity"><span class="badge c-capacity"><svg><use href="#i-capacity"/></svg></span>Recognise and<br>build capacity</li>
    </ul>
    <svg class="abs" style="left:0;top:512px" width="209" height="192" aria-hidden="true">
      <path d="M0 10C70 0 140 16 209 6v186H0z" fill="var(--forest)"/>
    </svg>
    <svg class="abs" style="left:82px;top:546px" width="46" height="40" aria-hidden="true"><use href="#i-circle"/></svg>
    <p class="banner-foot-text">Stronger together.<br>Building resilient communities.<br>Supporting long-term<br>recovery and wellbeing.</p>
  </section>
  <p class="caption" style="left:1077px;top:760px">Pull Up Banner</p>

</main>
</body>
</html>
```